Young, dynamic furniture company needs a new business card design

We require a new business card design for our modern furniture company which supplies furniture and appliances to the property and development market.
Oakridge Interiors has become one of the leading furniture & appliance suppliers to the property market withing London. With over 10 years experience, we have increased our business to supply not only private landlords and managing agents, but also property developers, housing associations and local councils.
We offer not only a complete range of furniture which includes beds, wardrobes, dining sets and sofas, but also a high quality, full delivery and assembly service to help you with all our furnishing needs.

Target Market(s)

Private landlords, estate agents, letting agents, property management companies

Industry/Entity Type

Business

Contact Information for Business Card

Name,
Title,
Address,
Mobile,
Telephone,
Fax, Website, email address

Font styles to use
Sans Serif

Colors
3176b5
0555a3
85abd2
cfdeed

Requirements
Must have
• All the above information for each of our staff, along with our logo

```html
<!DOCTYPE html>
<html lang="en">
<head>
<meta charset="utf-8">
<title>Oakridge Interiors – Business Card</title>
<link rel="stylesheet" href="https://fonts.googleapis.com/css2?family=Montserrat:wght@400;500;600;700&family=Ubuntu:wght@300;400&display=swap">
<style>
  :root {
    --blue-mid: #3176b5;
    --blue-deep: #0555a3;
    --blue-soft: #85abd2;
    --blue-pale: #cfdeed;
    --blue-night: #1b3d86;
    --ink: #2b2b2e;
    --ink-soft: #55565b;
    --paper: #ffffff;
    --paper-shade: #eef0f2;
    --stage: #e4e6ea;
  }
  * { box-sizing: border-box; margin: 0; padding: 0; }
  html, body { width: 1200px; height: 780px; overflow: hidden; }
  body {
    background: var(--stage);
    font-family: "Montserrat", sans-serif;
    position: relative;
  }
  .card {
    position: absolute;
    top: 236px;
    width: 540px;
    height: 309px;
    border-radius: 22px;
    overflow: hidden;
    box-shadow: 0 10px 26px rgba(0,0,0,0.18);
  }

  /* Front */
  .card--front {
    left: 36px;
    background: linear-gradient(135deg, var(--paper) 40%, var(--paper-shade) 100%);
  }
  .brand {
    position: absolute;
    top: 42px;
    left: 0;
    right: 0;
    text-align: center;
  }
  .brand__row {
    display: inline-flex;
    align-items: center;
    gap: 10px;
  }
  .brand__square {
    width: 18px;
    height: 18px;
    background: var(--blue-mid);
  }
  .brand__name {
    font-size: 24px;
    font-weight: 500;
    letter-spacing: 1.5px;
    color: var(--ink);
    text-transform: uppercase;
  }
  .brand__tagline {
    margin-top: 6px;
    font-size: 10px;
    font-weight: 500;
    letter-spacing: 2px;
    color: var(--ink-soft);
    text-transform: uppercase;
  }
  .person {
    position: absolute;
    left: 36px;
    top: 150px;
  }
  .person__name {
    font-size: 19px;
    font-weight: 700;
    letter-spacing: 1px;
    text-transform: uppercase;
    color: var(--blue-deep);
  }
  .person__name .surname { color: var(--blue-mid); }
  .person__title {
    font-size: 13px;
    font-weight: 500;
    color: var(--ink-soft);
    margin-top: 2px;
  }
  .contact {
    position: absolute;
    right: 34px;
    bottom: 30px;
    text-align: right;
    font-size: 12.5px;
    font-weight: 500;
    color: var(--ink);
    line-height: 1.7;
  }
  .contact .label { color: var(--blue-deep); font-weight: 700; }
  .contact .sep { color: var(--blue-deep); margin: 0 5px; }

  /* Back */
  .card--back {
    left: 624px;
    background: linear-gradient(150deg, var(--blue-deep) 0%, var(--blue-night) 100%);
    font-family: "Ubuntu", sans-serif;
    color: var(--paper);
  }
  .card--back .tone {
    position: absolute;
    inset: 0;
    background: linear-gradient(115deg, rgba(133,171,210,0) 35%, rgba(133,171,210,0.16) 60%, rgba(133,171,210,0) 85%);
  }
  .back__title {
    position: absolute;
    left: 40px;
    top: 62px;
    font-size: 38px;
    font-weight: 300;
    letter-spacing: 1.5px;
    text-transform: uppercase;
  }
  .back__tagline {
    position: absolute;
    left: 42px;
    top: 112px;
    font-size: 20px;
    font-weight: 300;
    letter-spacing: 1px;
    text-transform: uppercase;
    color: var(--blue-pale);
  }
  .back__address {
    position: absolute;
    left: 42px;
    bottom: 44px;
    font-size: 13.5px;
    font-weight: 400;
    line-height: 1.7;
  }
  .back__address .venue { color: var(--paper); }
  .back__address .street { color: var(--blue-pale); }
</style>
</head>
<body>

  <section class="card card--front" aria-label="Business card front">
    <div class="brand">
      <div class="brand__row">
        <span class="brand__square"></span>
        <span class="brand__name">Oakridge Interiors</span>
      </div>
      <div class="brand__tagline">Trade Furniture Solutions</div>
    </div>

    <div class="person">
      <div class="person__name">Marcus <span class="surname">Ellery</span></div>
      <div class="person__title">Managing Director</div>
    </div>

    <div class="contact">
      <div><span class="label">T:</span> 020 7946 0123<span class="sep">|</span><span class="label">F:</span> 020 7946 0124<span class="sep">|</span><span class="label">M:</span> 07700 90 04 82</div>
      <div><span class="label">E:</span> marcus@oakridgeint.co.uk<span class="sep">|</span>www.oakridgeint.co.uk</div>
    </div>
  </section>

  <section class="card card--back" aria-label="Business card back">
    <div class="tone"></div>
    <div class="back__title">Oakridge Interiors</div>
    <div class="back__tagline">Trade Furniture Solutions</div>
    <div class="back__address">
      <div class="venue">Trade Showroom &amp; Office</div>
      <div class="street">27B Fernhill Trade Park Northbrook London, N9 4QT</div>
    </div>
  </section>

</body>
</html>
```